Service Menu refresh 2018 Update of menu pricing

We currently have service menus as attached. We will be updating our look via our homepage image, our service menu and our in-house beverage and treatment menu.
We are a natural and sustainable hair salon group and moving more towards head spa which consists of treatments, beauty, tanning as well as your traditional hair services. Our imagery needs to reflect our efforts in spa treatments in the hair and scalp area and use natural materials and colours reflecting sustainability.
Velune is the brand we stock and promote.

Target Market(s)

Men or women interesting in personal maintenance with natural and organic products and using sustainable practises

Industry/Entity Type

Hair And Beauty

Font styles to use
Sans Serif
Other font styles liked:
• Arial or Helvetica

Colors
9acb3c
abd037
cadf82
ffffff

Requirements
Must have
• Name on the front cover, locations on back cover
Nice to have
• Prestige feel, reflect male and female clients
Should not have
• Bold artificial writing or any type of cartoon images.
• Same images as existing menu.

```html
<!DOCTYPE html>
<html lang="en">
<head>
<meta charset="utf-8">
<title>Leafwell Hair Studios — Service Menu</title>
<link href="https://fonts.googleapis.com/css2?family=Cabin:wght@400;600;700&family=Oswald:wght@500&display=swap" rel="stylesheet">
<style>
:root{
  --stage:#8a8c8f;
  --leaf:#9acb3c;
  --lime:#abd037;
  --pale:#cadf82;
  --white:#ffffff;
  --forest:#1f4a16;
  --ink:#1a1a1a;
  --panel:#f3f3f3;
  --bar:#cfcfcf;
  --bar-light:#dedede;
}
*{box-sizing:border-box;margin:0;padding:0}
html,body{width:1200px;height:1200px;overflow:hidden}
body{background:var(--stage);position:relative;font-family:"Cabin",Arial,sans-serif;color:var(--ink)}
.card{position:absolute;box-shadow:0 6px 16px rgba(0,0,0,.35);overflow:hidden}

/* front cover */
.cover{left:282px;top:136px;width:636px;height:452px}
.cover-photo{position:absolute;inset:0;background:radial-gradient(ellipse at 55% 55%,#6a4a36 0%,#3b2f25 35%,#26301f 70%,#1a2016 100%)}
.cover-foliage{position:absolute;right:0;top:0;width:200px;height:452px;background:linear-gradient(200deg,#8fe0a8 0%,#4fa35c 45%,#2f6b35 100%);opacity:.9;border-top-left-radius:120px 260px}
.cover-frame{position:absolute;left:9px;top:8px;right:9px;bottom:8px;border:1px solid rgba(255,255,255,.55)}
.cover-mark{position:absolute;left:50px;top:70px;width:60px;height:60px;border-radius:50%;background:var(--lime)}
.cover-name{position:absolute;left:130px;top:76px;font-weight:600;font-size:30px;color:var(--white);line-height:1.05;width:260px}
.cover-web{position:absolute;left:30px;top:421px;font-size:11.5px;color:var(--white)}

/* back menu */
.menu{left:280px;top:630px;width:642px;height:458px;background:var(--white);border-right:5px solid var(--leaf)}
.menu::after{content:"";position:absolute;left:128px;right:0;bottom:0;height:4px;background:var(--leaf)}
.menu-panel{position:absolute;left:0;right:0;top:78px;bottom:4px;background:var(--panel)}
.menu-foliage{position:absolute;left:0;top:0;width:92px;height:458px;background:linear-gradient(180deg,#6f8a3a 0%,#4d7a45 35%,rgba(77,122,69,.2) 60%,#3f7a4c 85%,#2e5e3a 100%);border-top-right-radius:60px 200px;border-bottom-right-radius:80px 140px}
.menu-brand{position:absolute;left:400px;top:18px;display:flex;align-items:center;gap:8px}
.menu-brand .dot{width:44px;height:44px;border-radius:50%;background:var(--leaf)}
.menu-brand .name{font-weight:600;font-size:17px;color:var(--ink);line-height:1.05}

.col{position:absolute;width:28px;background:var(--bar)}
.col.alt{background:var(--bar-light)}
.col-head{position:absolute;left:0;top:0;width:100%;height:24px;background:var(--ink);color:var(--lime);font-weight:700;font-size:11px;display:flex;align-items:center;justify-content:center}

.t{position:absolute;white-space:nowrap}
.h1{font-weight:700;font-size:18px;color:var(--forest);line-height:1.05}
.h2{font-weight:700;font-size:11.5px;color:var(--forest);letter-spacing:.3px}
.item{font-size:8.5px}
.p{font-family:"Oswald",Arial,sans-serif;font-weight:500;font-size:8px;width:28px;text-align:center}
.note{font-size:6px;line-height:8px}
</style>
</head>
<body>

<section class="card cover" aria-label="Front cover">
  <div class="cover-photo" role="img" aria-label="Photograph of a woman with long auburn hair wearing a wide-brim hat among greenhouse plants"></div>
  <div class="cover-foliage" role="img" aria-label="Engraved-style illustration of tropical leaves and ferns"></div>
  <div class="cover-frame"></div>
  <div class="cover-mark"></div>
  <div class="cover-name">Leafwell Hair Studios</div>
  <div class="cover-web">www.leafwellhair.com.au</div>
</section>

<section class="card menu" aria-label="Service menu">
  <div class="menu-panel"></div>
  <div class="menu-foliage" role="img" aria-label="Engraved-style illustration of fern fronds and leaves"></div>
  <div class="menu-brand"><span class="dot"></span><span class="name">Leafwell Hair Studios</span></div>

  <!-- cut & blowdry columns -->
  <div class="col" style="left:211px;top:77px;height:345px"><span class="col-head">S</span></div>
  <div class="col alt" style="left:244px;top:77px;height:345px"><span class="col-head">M</span></div>
  <div class="col" style="left:278px;top:77px;height:345px"><span class="col-head">L</span></div>
  <div class="col alt" style="left:310px;top:77px;height:345px"><span class="col-head">XL</span></div>

  <div class="t h1" style="left:108px;top:70px">CUT &amp;<br>BLOWDRY</div>

  <div class="t h2" style="left:108px;top:116px">LADIES FRINGE</div>
  <div class="t p" style="left:211px;top:119px">$77</div><div class="t p" style="left:244px;top:119px">$88</div><div class="t p" style="left:278px;top:119px">$99</div><div class="t p" style="left:310px;top:119px">$110</div>
  <div class="t item" style="left:108px;top:136px">Trim</div><div class="t p" style="left:211px;top:136px">$25</div>
  <div class="t item" style="left:108px;top:147px">Restyle</div><div class="t p" style="left:211px;top:147px">$35</div>

  <div class="t h2" style="left:108px;top:168px">MENS</div>
  <div class="t item" style="left:108px;top:186px">Single clipper</div><div class="t p" style="left:211px;top:186px">$28</div>
  <div class="t item" style="left:108px;top:197px">Style cut</div><div class="t p" style="left:211px;top:197px">$42</div>

  <div class="t h2" style="left:108px;top:212px">CHILDREN</div>
  <div class="t item" style="left:108px;top:233px">10 and under</div><div class="t p" style="left:211px;top:233px">$24</div>
  <div class="t item" style="left:108px;top:247px">11-16 male</div><div class="t p" style="left:211px;top:247px">$32</div>
  <div class="t item" style="left:108px;top:261px">11-16 female</div><div class="t p" style="left:211px;top:261px">$48</div>
  <div class="t item" style="left:108px;top:274px">add a wash</div><div class="t p" style="left:211px;top:274px">$5</div><div class="t p" style="left:244px;top:274px">$57</div><div class="t p" style="left:278px;top:274px">$67</div><div class="t p" style="left:310px;top:274px">$77</div>

  <div class="t h2" style="left:108px;top:291px">BLOWDRY</div><div class="t p" style="left:211px;top:293px">$47</div>
  <div class="t item" style="left:108px;top:310px">Shampoo &amp; dry off</div><div class="t p" style="left:211px;top:310px">$25</div>

  <div class="t h2" style="left:108px;top:327px">TREATMENTS</div>
  <div class="t item" style="left:108px;top:348px">Deep treatment</div><div class="t p" style="left:211px;top:348px">$35</div>
  <div class="t item" style="left:108px;top:360px">Head spa ritual</div><div class="t p" style="left:211px;top:360px">$65</div>

  <div class="t h2" style="left:108px;top:373px">UPSTYLE</div>
  <div class="t item" style="left:108px;top:394px">45 minutes</div><div class="t p" style="left:211px;top:394px">$85</div>
  <div class="t item" style="left:108px;top:406px">60 minutes</div><div class="t p" style="left:211px;top:406px">$120</div>

  <!-- colour columns -->
  <div class="col" style="left:492px;top:102px;height:324px"><span class="col-head">S</span></div>
  <div class="col alt" style="left:525px;top:102px;height:324px"><span class="col-head">M</span></div>
  <div class="col" style="left:558px;top:102px;height:324px"><span class="col-head">L</span></div>
  <div class="col alt" style="left:590px;top:102px;height:324px"><span class="col-head">XL</span></div>

  <div class="t h1" style="left:362px;top:106px">COLOUR</div>
  <div class="t item" style="left:362px;top:139px">Regrowth</div><div class="t p" style="left:492px;top:139px">$83</div>
  <div class="t item" style="left:362px;top:153px">FULL colour tint</div><div class="t p" style="left:492px;top:153px">$125</div><div class="t p" style="left:525px;top:153px">$165</div><div class="t p" style="left:558px;top:153px">$145</div><div class="t p" style="left:590px;top:153px">$185</div>
  <div class="t item" style="left:362px;top:166px">REGROWTH lightening</div><div class="t p" style="left:492px;top:166px">$165</div><div class="t p" style="left:525px;top:166px">$209</div><div class="t p" style="left:558px;top:166px">$189</div><div class="t p" style="left:590px;top:166px">$229</div>
  <div class="t item" style="left:362px;top:180px">BALAYAGE/OMBRE</div><div class="t p" style="left:525px;top:180px">$375</div><div class="t p" style="left:558px;top:180px">$275</div><div class="t p" style="left:590px;top:180px">$475</div>

  <div class="t h2" style="left:362px;top:204px">FLORANECTAR</div>
  <div class="t item" style="left:362px;top:228px">Regrowth</div><div class="t p" style="left:492px;top:233px">$99</div>
  <div class="t p" style="left:525px;top:239px">$175</div><div class="t p" style="left:558px;top:239px">$195</div><div class="t p" style="left:590px;top:239px">$205</div>
  <div class="t p" style="left:492px;top:244px">$155</div>
  <div class="t item" style="left:362px;top:250px">FULL colour tint</div>

  <div class="t h1" style="left:362px;top:275px">FOILS</div>
  <div class="t item" style="left:362px;top:303px">Single</div><div class="t p" style="left:492px;top:303px">$11</div><div class="t p" style="left:525px;top:303px">$13</div><div class="t p" style="left:558px;top:303px">$17</div><div class="t p" style="left:590px;top:303px">$22</div>
  <div class="t item" style="left:362px;top:315px">1/4 head</div><div class="t p" style="left:492px;top:315px">$135</div><div class="t p" style="left:525px;top:315px">$155</div><div class="t p" style="left:558px;top:315px">$175</div><div class="t p" style="left:590px;top:315px">$195</div>
  <div class="t item" style="left:362px;top:327px">1/2 head</div><div class="t p" style="left:492px;top:327px">$185</div><div class="t p" style="left:525px;top:327px">$205</div><div class="t p" style="left:558px;top:327px">$235</div><div class="t p" style="left:590px;top:327px">$265</div>
  <div class="t item" style="left:362px;top:338px">Full head</div><div class="t p" style="left:492px;top:338px">$235</div><div class="t p" style="left:525px;top:338px">$265</div><div class="t p" style="left:558px;top:338px">$315</div><div class="t p" style="left:590px;top:338px">$355</div>

  <div class="t h1" style="left:362px;top:360px">STRAIGHT</div>
  <div class="t item" style="left:362px;top:381px;font-weight:700">SMOOTHLINE 5mm SYSTEM</div>
  <div class="t p" style="left:492px;top:381px">$365</div><div class="t p" style="left:525px;top:381px">$445</div><div class="t p" style="left:558px;top:381px">$535</div><div class="t p" style="left:590px;top:381px">$565</div>
  <div class="t note" style="left:362px;top:400px">• Includes colour match &amp; toner<br>• Minimum 6 foils without colour<br>• Minimum charge on a Sunday is $40</div>
</section>

</body>
</html>
```